Brightwave Reach - Business Card

We need a business card for a Social Media Marketing company that specializes in online marketing for small businesses in Canada using common Social Media platforms such as Pixlora, Chatterly, Blinkpost & Quibber.

I have uploaded a copy of our logo which I would like utilized in the business card. We would like the business card to be modern yet classy design.

Our website is www.brightwavereach.ca

Industry/Entity Type

Marketing

Contact Information for Business Card

Email: info@brightwavereach.ca
Website: www.brightwavereach.ca
Telephone: 604-555-0193

Colors

Designer to choose colors to be used in the design.

Requirements
Must have
• Social Media icons on reverse
• Please add some designs with color.

```html
<!DOCTYPE html>
<html lang="en">
<head>
<meta charset="utf-8">
<title>Brightwave Reach – Business Card</title>
<link rel="stylesheet" href="https://fonts.googleapis.com/css2?family=Roboto+Condensed:wght@400;500;700&family=Roboto:wght@400&display=swap">
<style>
  :root {
    --backdrop: #e4e4e3;
    --card-light: #f4f4f3;
    --card-dark: #3d4043;
    --ink: #3a3d40;
    --ink-muted: #a9abad;
    --ink-body: #45484b;
    --paper-white: #f2f2f2;
  }
  * { margin: 0; padding: 0; box-sizing: border-box; }
  html, body { width: 1200px; height: 960px; overflow: hidden; }
  body { background: var(--backdrop); position: relative; font-family: "Roboto", sans-serif; }

  .card { position: absolute; width: 601px; height: 343px; }
  .card--front { left: 314px; top: 113px; background: var(--card-light); }
  .card--back { left: 311px; top: 472px; background: var(--card-dark); }

  .front__accent { position: absolute; left: 0; top: 196px; width: 12px; height: 38px; background: var(--ink); }

  .brand-name {
    position: absolute; left: 372px; top: 66px; width: 190px;
    font-family: "Roboto Condensed", sans-serif; font-weight: 700;
    font-size: 29px; line-height: 30px; text-align: center;
    color: #4a4d50; text-transform: uppercase; letter-spacing: 0.5px;
  }

  .person { position: absolute; left: 47px; top: 192px; }
  .person__name {
    font-family: "Roboto Condensed", sans-serif; font-weight: 500;
    font-size: 21px; color: var(--ink); line-height: 26px;
  }
  .person__role {
    font-family: "Roboto Condensed", sans-serif; font-weight: 400;
    font-size: 15px; color: var(--ink-muted); line-height: 20px; letter-spacing: 0.3px;
  }

  .contacts { position: absolute; left: 48px; top: 246px; list-style: none; }
  .contacts li {
    display: flex; align-items: center; height: 19.5px;
    font-size: 14px; color: var(--ink-body);
  }
  .contacts svg { width: 12px; height: 12px; margin-right: 10px; fill: var(--ink); }

  .back__brand {
    position: absolute; left: 0; right: 0; top: 140px; text-align: center;
    font-family: "Roboto Condensed", sans-serif; font-weight: 700;
    font-size: 34px; color: var(--paper-white); text-transform: uppercase; letter-spacing: 1px;
  }

  .socials {
    position: absolute; left: 0; right: 0; top: 286px;
    display: flex; align-items: center; justify-content: center; gap: 12px;
  }
  .socials__rule { width: 90px; height: 1px; }
  .socials__rule--left { background: linear-gradient(to right, transparent, #cfd0d1); }
  .socials__rule--right { background: linear-gradient(to left, transparent, #cfd0d1); }
  .social { display: flex; align-items: center; gap: 5px; color: var(--paper-white); font-size: 12px; }
  .social__dot { width: 14px; height: 14px; border: 1.5px solid var(--paper-white); border-radius: 50%; }
</style>
</head>
<body>
  <section class="card card--front">
    <div class="front__accent"></div>
    <div class="brand-name">Brightwave Reach</div>

    <div class="person">
      <div class="person__name">DANIEL HARPER</div>
      <div class="person__role">CEO/FOUNDER</div>
    </div>

    <ul class="contacts">
      <li>
        <svg viewBox="0 0 24 24"><path d="M6.6 10.8a15.1 15.1 0 0 0 6.6 6.6l2.2-2.2c.3-.3.7-.4 1-.2 1.1.4 2.3.6 3.6.6.6 0 1 .4 1 1V20c0 .6-.4 1-1 1A17 17 0 0 1 3 4c0-.6.4-1 1-1h3.5c.6 0 1 .4 1 1 0 1.3.2 2.5.6 3.6.1.3 0 .7-.2 1z"/></svg>
        604-555-0193
      </li>
      <li>
        <svg viewBox="0 0 24 24"><path d="M2 5h20v14H2z M3 6l9 7 9-7" fill="none" stroke="#3a3d40" stroke-width="0"/><path d="M2 5h20v2l-10 7L2 7z"/><path d="M2 9l10 7 10-7v10H2z"/></svg>
        info@brightwavereach.ca
      </li>
      <li>
        <svg viewBox="0 0 24 24"><circle cx="12" cy="12" r="10"/><path d="M7 8c2 0 3 1 3 3s-2 2-1 4 1 4 0 5M15 4c0 2 1 3 3 3s2 2 1 4" fill="none" stroke="#f4f4f3" stroke-width="2"/></svg>
        www.brightwavereach.ca
      </li>
    </ul>
  </section>

  <section class="card card--back">
    <div class="back__brand">Brightwave Reach</div>
    <div class="socials">
      <span class="socials__rule socials__rule--left"></span>
      <span class="social"><span class="social__dot"></span>Chatterly</span>
      <span class="social"><span class="social__dot"></span>Pixlora</span>
      <span class="social"><span class="social__dot"></span>Quibber</span>
      <span class="socials__rule socials__rule--right"></span>
    </div>
  </section>
</body>
</html>
```